Website redesign - vorelmik.com

We are looking to do a full redesign of vorelmik.com. Need a designer to come up overall layout and 3 specific pages and 3 different hero images.
Wireframes for the 3 pages are attached as well as site images. You don't have to follow the wireframes exactly, but instead the wireframe is there to show you the information that needs to be on each page. Feel free to rearrange as needed.
Our target market is self taught engineers. So definitely I want a more casual feel to it. I'm ok with fun bold colors as well. Really like websites that have the infinite scroll look/feel to them.
Looking to find a designer who will produce HTML and potentially even implement the HTML into our site checked in code.
HTML Code should be responsive/mobile first leveraging Bootstrap 4.
Attached files include:
0) Wireframe PDF
https://files.plomwerk.net/d/7Kx2pQmW9zLr4TbN8vYc3HsE5fJ/view?mode=share
1) Vorelmik Images zip 1
https://files.plomwerk.net/d/4Gt8nRvB2wQx6MkZ1pLd9YaC7hU/view?mode=share
2) Vorelmik Images zip 2
https://files.plomwerk.net/d/9Jw3sTcF5yNv1HqX8rKb2ZeM6dP/view?mode=share
Target Market(s)
I sell DIY Waterproof Electronics enclosures. Target audience is self taught DIY engineers
Coding
Coded - Design and coding required
Number of Pages Required
3 page
Colors
Designer to choose colors to be used in the design.
Look and feel

```html
<!DOCTYPE html>
<html lang="en">
<head>
<meta charset="utf-8">
<title>Vorelmik — Waterproof Project Boxes</title>
<link rel="stylesheet" href="https://fonts.googleapis.com/css2?family=Audiowide&family=Roboto:wght@400;500;700&display=swap">
<style>
:root{
  --blue:#0a00f2;
  --lime:#c9d300;
  --lime-deep:#c4cc0a;
  --ink:#1a1a1a;
  --muted:#444;
  --lavender:#eceefa;
  --card:#f6f4f2;
  --line:#d9d9d9;
  --white:#ffffff;
}
*{box-sizing:border-box;margin:0;padding:0}
html,body{width:1200px;height:4710px;overflow:hidden}
body{position:relative;font-family:"Roboto",sans-serif;color:var(--ink);background:var(--white)}
.display{font-family:"Audiowide",sans-serif;text-transform:uppercase;letter-spacing:0;font-weight:400;white-space:nowrap}
.section-title{font-size:26px;line-height:36px}
.btn{position:absolute;display:flex;align-items:center;justify-content:center;background:var(--lime);color:var(--ink);font:500 16px "Roboto",sans-serif;border-radius:22px;text-transform:uppercase;text-decoration:none}

/* header */
.site-header{position:absolute;left:0;top:0;width:1200px;height:73px;background:var(--white)}
.brand{position:absolute;display:flex;align-items:center;gap:8px;font-family:"Audiowide",sans-serif;color:var(--blue)}
.brand .dot{width:10px;height:10px;border-radius:50%;background:var(--lime)}
.site-header .brand{left:88px;top:16px;font-size:32px}
.main-nav{position:absolute;left:289px;top:28px;display:flex;gap:36px;font:500 15px "Roboto",sans-serif;color:#333}
.account{position:absolute;right:90px;top:22px;display:flex;align-items:center;gap:18px;font:500 15px "Roboto",sans-serif;color:#333}
.account .signup{background:var(--lime);padding:6px 20px;border-radius:16px}

/* hero */
.hero{position:absolute;left:0;top:73px;width:1200px;height:744px;background:var(--blue);overflow:hidden}
.hero h1{position:absolute;left:88px;top:258px;color:var(--white);font-size:34px;line-height:44px}
.hero .price{position:absolute;left:88px;top:398px;color:var(--lime);font-size:50px;line-height:50px}
.hero .btn{left:88px;top:470px;width:184px;height:42px}
.hero-pill{position:absolute;left:960px;top:139px;width:150px;height:488px;border-radius:75px;background:var(--white)}
.hero-photo{position:absolute;left:620px;top:150px;width:470px;height:420px;border-radius:30px;background:radial-gradient(ellipse at 50% 50%,#6b6f76 0%,#3b3f47 45%,rgba(40,44,60,0) 75%)}
.slider-dots{position:absolute;display:flex;gap:8px}
.slider-dots i{width:9px;height:9px;border-radius:50%;background:var(--white)}
.slider-dots i.on{background:var(--lime)}

/* designer */
.designer{position:absolute;left:0;top:817px;width:1200px;height:498px;background:var(--lavender)}
.video{position:absolute;left:124px;top:108px;width:474px;height:287px;border-radius:16px;background:linear-gradient(135deg,#2a2d33,#6f7479 45%,#2c5a3a 70%,#202226);box-shadow:0 24px 40px rgba(40,40,80,.25)}
.video .play{position:absolute;left:205px;top:120px;width:60px;height:50px;border-radius:10px;background:#e8222a}
.video .play svg{position:absolute;left:22px;top:15px}
.designer h2{position:absolute;left:665px;top:172px}
.designer .btn{left:665px;top:301px;width:172px;height:40px}

/* kits */
.kits h2{position:absolute;left:0;top:1403px;width:1200px;text-align:center}
.kits .btn{left:514px;top:1530px;width:172px;height:42px}
.kit-card{position:absolute;border-radius:16px;background:var(--card)}
.kit-card .shot{position:absolute;inset:12%;border-radius:10px;background:linear-gradient(160deg,#d9d9d6,#8b8f8a 55%,#cfcfcb)}
.divider{position:absolute;left:88px;top:1981px;width:1024px;height:1px;background:var(--line)}

/* makers */
.makers h2{position:absolute;left:128px;top:2140px}
.features{position:absolute;left:128px;top:2260px;list-style:none;font-size:16px;line-height:30px;color:var(--muted)}
.features li{padding-left:22px;position:relative}
.features li::before{content:"";position:absolute;left:2px;top:12px;width:6px;height:6px;border-radius:50%;background:#999}
.makers .btn{left:128px;top:2402px;width:172px;height:40px}
.maker-tab{position:absolute;left:1010px;top:2157px;width:100px;height:218px;border-radius:22px;background:var(--blue)}
.maker-photo{position:absolute;left:667px;top:2072px;width:397px;height:396px;border-radius:20px;background:linear-gradient(140deg,#6f5a43,#b99676 40%,#8b6b4c 75%,#5a4633)}

/* testimonials */
.testimonials{position:absolute;left:0;top:2593px;width:1200px;height:460px;background:var(--lime-deep)}
.testimonials h2{position:absolute;left:0;top:95px;width:1200px;text-align:center}
.quote{position:absolute;top:155px;width:490px;height:164px;background:var(--white);border-radius:14px;font-size:14.5px;line-height:23px;color:#333}
.quote p{position:absolute;left:34px;top:30px;width:340px}
.quote .who{position:absolute;right:30px;bottom:22px;font-weight:500;color:var(--ink);font-size:16px}
.quote svg{position:absolute;left:40px;bottom:-26px}

/* examples */
.examples h2{position:absolute;left:0;top:3140px;width:1200px;text-align:center;line-height:34px}
.example{position:absolute;width:249px}
.example .frame{width:249px;height:290px;border-radius:16px;background:var(--card);position:relative}
.example .frame .shot{position:absolute;left:20%;top:25%;width:60%;height:45%;border-radius:8px}
.example .name{margin-top:28px;font:500 16px/22px "Roboto",sans-serif;color:var(--ink)}
.grey{background:linear-gradient(160deg,#dcdcda,#9c9e9a)}
.board{background:linear-gradient(160deg,#d6d6d2,#6a6f66 50%,#c9c9c4)}
.dark{background:linear-gradient(160deg,#4a4d52,#202226)}
.clear{background:linear-gradient(160deg,#dcd8f0,#a9a3cf)}
.pink{background:linear-gradient(160deg,#f3e6ee,#d9c6d4)}
.ammo{background:linear-gradient(160deg,#2f3a30,#141a15)}

/* footer */
.site-footer{position:absolute;left:0;top:4435px;width:1200px;height:275px;background:var(--blue)}
.site-footer .brand{left:0;right:0;top:55px;justify-content:center;color:var(--white);font-size:50px}
.site-footer .copy{position:absolute;left:0;top:148px;width:1200px;text-align:center;color:var(--white);font:500 16px "Roboto",sans-serif}
.socials{position:absolute;left:563px;top:180px;display:flex;gap:12px}
.socials i{width:30px;height:30px;border-radius:50%;background:#3b36ff}
.to-top{position:absolute;left:1135px;top:188px;width:32px;height:32px;border-radius:50%;background:var(--lime)}
</style>
</head>
<body>

<header class="site-header">
  <div class="brand"><span class="dot"></span>Vorelmik</div>
  <nav class="main-nav"><span>Get Started</span><span>Designs</span><span>FAQs</span><span>Videos</span><span>Contact Us</span></nav>
  <div class="account"><span>Sign in</span><span class="signup">Sign up</span></div>
</header>

<section class="hero">
  <h1 class="display">Waterproof project<br>boxes customized<br>to your exact needs.</h1>
  <div class="price display">$1200</div>
  <a class="btn" href="#">Get Started</a>
  <div class="hero-pill"></div>
  <div class="hero-photo" role="img" aria-label="Assembled electronics mounting plate with controller boards and wiring"></div>
  <div class="slider-dots" style="left:578px;top:688px"><i class="on"></i><i></i><i></i></div>
</section>

<section class="designer">
  <div class="video" role="img" aria-label="Video still of power supplies and controller board inside an enclosure">
    <div class="play"><svg width="18" height="20" viewBox="0 0 18 20"><path d="M0 0L18 10L0 20Z" fill="#fff"/></svg></div>
  </div>
  <h2 class="display section-title">Customize your<br>project box using our<br>designer</h2>
  <a class="btn" href="#">Get Started</a>
</section>

<section class="kits">
  <h2 class="display section-title">Mounting kits for all the popular<br>water proof project boxes wit h many<br>sizes to choose from</h2>
  <a class="btn" href="#">Get Started</a>
  <div class="kit-card" style="left:265px;top:1643px;width:170px;height:197px"><div class="shot" role="img" aria-label="Open enclosure with controller board"></div></div>
  <div class="kit-card" style="left:765px;top:1643px;width:170px;height:197px"><div class="shot" role="img" aria-label="Controller boards on mounting plate"></div></div>
  <div class="kit-card" style="left:417px;top:1608px;width:366px;height:267px"><div class="shot" role="img" aria-label="Open waterproof box with power supply mounted inside"></div></div>
</section>

<div class="divider"></div>

<section class="makers">
  <h2 class="display section-title">Vorelmik waterproof<br>project boxes were built<br>by makers for makers</h2>
  <ul class="features">
    <li>Design to your specifications</li>
    <li>Maker components: Tinkerduo, Berrybrick Pi, Voltwell Power</li>
    <li>Detailed build instructions, videos, walkthroughs</li>
    <li>DIY made to look professional</li>
  </ul>
  <a class="btn" href="#">Get Started</a>
  <div class="maker-tab"></div>
  <div class="maker-photo" role="img" aria-label="Mounting plate kit with boards and hardware on a wooden bench"></div>
</section>

<section class="testimonials">
  <h2 class="display section-title">What our customers have to say</h2>
  <div class="quote" style="left:96px">
    <p>Great work at a reasonable cost.<br>I can't recommend them enough.<br><span style="display:block;margin-top:4px">If you're doing custom boxes for light shows, this is where you go.</span></p>
    <span class="who">-Ansel M</span>
    <svg width="30" height="28" viewBox="0 0 30 28"><path d="M0 0H30L4 28Z" fill="#fff"/></svg>
  </div>
  <div class="quote" style="left:613px">
    <p>Fantastic service/product..<br>whether you simply generate the design and do all of the fabrication yourself or simply order the kits.</p>
    <span class="who">-Corin T.</span>
    <svg width="30" height="28" viewBox="0 0 30 28"><path d="M0 0H30L4 28Z" fill="#fff"/></svg>
  </div>
  <div class="slider-dots" style="left:580px;top:380px"><i class="on" style="background:#fff"></i><i style="opacity:.6"></i><i style="opacity:.6"></i></div>
</section>

<section class="examples">
  <h2 class="display section-title">See real examples from<br>our customers</h2>

  <div class="example" style="left:207px;top:3225px"><div class="frame"><div class="shot grey" role="img" aria-label="Closed grey enclosure"></div></div><div class="name">KRX-72 w/ P16v3 +<br>Expansion board</div></div>
  <div class="example" style="left:476px;top:3225px"><div class="frame"><div class="shot board" role="img" aria-label="Open enclosure with controller board"></div></div><div class="name">KRX-72 w/ P16v3 +<br>Expansion board</div></div>
  <div class="example" style="left:744px;top:3225px"><div class="frame"><div class="shot dark" role="img" aria-label="Boards on dark mounting plate"></div></div><div class="name">KRX-72 w/ P16v3 +<br>Expansion board</div></div>

  <div class="example" style="left:207px;top:3610px"><div class="frame"><div class="shot board" role="img" aria-label="Open enclosure with power supply"></div></div><div class="name">KRX-72 w/ P16v3 +<br>Expansion board</div></div>
  <div class="example" style="left:476px;top:3610px"><div class="frame"><div class="shot dark" role="img" aria-label="Power supply on dark mounting plate"></div></div><div class="name">KRX-72 w/ P16v3 +<br>Expansion board</div></div>
  <div class="example" style="left:744px;top:3610px"><div class="frame"><div class="shot clear" role="img" aria-label="Translucent blue enclosure"></div></div><div class="name">KRX-72 w/ P16v3 +<br>Expansion board</div></div>

  <div class="example" style="left:207px;top:3993px"><div class="frame"><div class="shot pink" role="img" aria-label="Translucent pink enclosure"></div></div><div class="name">KRX-72 w/ P16v3 +<br>Expansion board</div></div>
  <div class="example" style="left:476px;top:3993px"><div class="frame"><div class="shot ammo" role="img" aria-label="Dark green rugged case"></div></div><div class="name">KRX-72 w/ P16v3 +<br>Expansion board</div></div>
  <div class="example" style="left:744px;top:3993px"><div class="frame"><div class="shot dark" role="img" aria-label="Stacked boards on dark mounting plate"></div></div><div class="name">KRX-72 w/ P16v3 +<br>Expansion board</div></div>
</section>

<footer class="site-footer">
  <div class="brand"><span class="dot"></span>Vorelmik</div>
  <div class="copy">Copyright 2020 @ vorelmik designer.</div>
  <div class="socials"><i></i><i></i></div>
  <div class="to-top"></div>
</footer>

</body>
</html>
```